Solar Company Bussiness Card

I need a 2 sided business card and would like a .psd and any font files for each side of the card. I would like my logo used, it should be attached with the fonts. I'm not opposed to the font colors with the logo being changed.

On the sample design, I'd like the following:

Marcus Dellow
President
Phone: 555-382-9174
www.brightvanepower.example

As I've recently opened in a 2nd market, I'm not sure about an address as I currently have 2 of them. I may actually get separate cards printed, one batch for each address, that's why I need the PSD file.
Updates

I'm very pleased with the response and designs I've received here for my business card. First and foremost, I'd like to thank everyone who took the time to submit a design. There truly are a lot of great designs in the bunch here and I'm having a little difficulty deciding. I will be reaching out to someone in the next day or two here to go to a final design. At this time, I'm not looking for any new concepts. If any of you do logos, I'm looking for a new logo for our sister entity, Dellow Partners, Inc. Thanks, Marcus Dellow

Reason: I'm not looking for any new designs at this point, but extending this deadline in order to give people I've asked a chance to re-submit items.

Industry/Entity Type

Business

```html
<!DOCTYPE html>
<html lang="en">
<head>
<meta charset="utf-8">
<title>Brightvane Power – Business Card</title>
<link rel="stylesheet" href="https://fonts.googleapis.com/css2?family=Exo+2:wght@400;500&display=swap">
<style>
  :root {
    --stage: #e9e7e3;
    --card-white: #ffffff;
    --brand-blue: #0b5aa3;
    --brand-blue-light: #3f8fd6;
    --ink-on-blue: #ffffff;
    --shadow: rgba(0, 0, 0, 0.18);
  }
  * { box-sizing: border-box; margin: 0; padding: 0; }
  html, body {
    width: 1200px; height: 870px; overflow: hidden;
    background: var(--stage);
    font-family: "Exo 2", sans-serif;
  }
  .stage {
    width: 1200px; height: 870px;
    display: flex; flex-direction: column;
    align-items: center; justify-content: center; gap: 40px;
  }
  .card {
    position: relative;
    width: 660px; height: 377px;
    border-radius: 4px;
    overflow: hidden;
    box-shadow: 0 6px 18px var(--shadow);
  }

  /* Front side */
  .card--front { background: var(--card-white); }
  .card-front__swoosh {
    position: absolute; inset: 0; width: 100%; height: 100%;
  }
  .brand {
    position: absolute; left: 90px; top: 166px;
    display: flex; align-items: center; gap: 14px;
  }
  .brand__mark {
    width: 40px; height: 40px; background: var(--brand-blue);
  }
  .brand__name {
    font-weight: 500; font-size: 38px; letter-spacing: 1px;
    color: var(--brand-blue);
  }

  /* Back side */
  .card--back { background: var(--brand-blue); color: var(--ink-on-blue); }
  .holder {
    position: absolute; left: 40px; top: 40px;
  }
  .holder__name {
    font-weight: 500; font-size: 30px; letter-spacing: 2px; text-transform: uppercase;
  }
  .holder__title {
    font-weight: 400; font-size: 18px; margin-top: 4px; padding-left: 70px;
  }
  .address {
    position: absolute; left: 250px; top: 153px;
    font-size: 17px; line-height: 24px;
  }
  .contacts {
    position: absolute; right: 36px; top: 150px;
    list-style: none; font-size: 17px;
  }
  .contacts__item {
    display: flex; align-items: center; justify-content: flex-end;
    gap: 12px; height: 30px;
  }
  .contacts__icon { width: 18px; height: 18px; fill: var(--ink-on-blue); }
  .contacts__item--web { margin-top: 8px; }
</style>
</head>
<body>
<main class="stage">

  <section class="card card--front" aria-label="Card front">
    <svg class="card-front__swoosh" viewBox="0 0 660 377" preserveAspectRatio="none" aria-hidden="true">
      <path d="M560 0 Q610 190 540 377 L660 377 L660 0 Z" fill="var(--brand-blue)"/>
      <path d="M548 0 Q598 190 528 377 L540 377 Q610 190 560 0 Z" fill="var(--brand-blue-light)"/>
    </svg>
    <div class="brand">
      <span class="brand__mark"></span>
      <span class="brand__name">Brightvane Power</span>
    </div>
  </section>

  <section class="card card--back" aria-label="Card back">
    <div class="holder">
      <h1 class="holder__name">Marcus Dellow</h1>
      <p class="holder__title">President</p>
    </div>

    <p class="address">Suite 4, 27 Harlow Road,<br>Carrow Bay</p>

    <ul class="contacts">
      <li class="contacts__item">555-382-9174
        <svg class="contacts__icon" viewBox="0 0 24 24" aria-hidden="true"><path d="M6.6 10.8a15 15 0 0 0 6.6 6.6l2.2-2.2a1 1 0 0 1 1-.25 11.4 11.4 0 0 0 3.6.57 1 1 0 0 1 1 1V20a1 1 0 0 1-1 1A17 17 0 0 1 3 4a1 1 0 0 1 1-1h3.5a1 1 0 0 1 1 1c0 1.25.2 2.450.57 3.6a1 1 0 0 1-.25 1z"/></svg>
      </li>
      <li class="contacts__item">555-382-9175
        <svg class="contacts__icon" viewBox="0 0 24 24" aria-hidden="true"><path d="M7 2h10a2 2 0 0 1 2 2v16a2 2 0 0 1-2 2H7a2 2 0 0 1-2-2V4a2 2 0 0 1 2-2zm0 3v13h10V5z"/></svg>
      </li>
      <li class="contacts__item">555-382-9176
        <svg class="contacts__icon" viewBox="0 0 24 24" aria-hidden="true"><path d="M6 2h9v6H6zM4 9h16a2 2 0 0 1 2 2v9H2v-9a2 2 0 0 1 2-2zm2 4v2h4v-2zm0 3v2h4v-2z"/></svg>
      </li>
      <li class="contacts__item">hello@brightvanepower.example
        <svg class="contacts__icon" viewBox="0 0 24 24" aria-hidden="true"><path d="M2 5h20v14H2zm2 2v.5l8 5 8-5V7zm0 2.8V17h16V9.8l-8 5z"/></svg>
      </li>
      <li class="contacts__item contacts__item--web">www.brightvanepower.example
        <svg class="contacts__icon" viewBox="0 0 24 24" aria-hidden="true"><path d="M12 2a10 10 0 1 0 0 20 10 10 0 0 0 0-20zm6.9 9h-3a15 15 0 0 0-1.3-5.8A8 8 0 0 1 18.9 11zM12 4c.9 1.2 1.8 3.6 1.9 7h-3.8c.1-3.4 1-5.8 1.9-7zM9.4 5.2A15 15 0 0 0 8.1 11h-3a8 8 0 0 1 4.3-5.8zM5.1 13h3a15 15 0 0 0 1.3 5.8A8 8 0 0 1 5.1 13zm6.9 7c-.9-1.2-1.8-3.6-1.9-7h3.8c-.1 3.4-1 5.8-1.9 7zm2.6-1.2a15 15 0 0 0 1.3-5.8h3a8 8 0 0 1-4.3 5.8z"/></svg>
      </li>
    </ul>
  </section>

</main>
</body>
</html>
```